Local Roofing/Construction company business needs new biz card design

We need a new business card design, current cards are from the start of this operation and generic at best. We are a local Construction Company (General Contractor) with a majority of our work originating from insurance claims-exterior finish work is the main focus (Roofs-Siding-Gutters etc). Heavily involved with homeowners and the low ball offers they receive from insurance company's after a insurable event takes place. I have attached some of our original logo file(s) below.

```html
<!DOCTYPE html>
<html lang="en">
<head>
<meta charset="utf-8">
<title>Ridgeline Construction – Business Card</title>
<link rel="stylesheet" href="https://fonts.googleapis.com/css2?family=Poppins:wght@400;600&family=Oswald:wght@500&display=swap">
<style>
  :root {
    --backdrop: #161819;
    --card: #0f1e22;
    --accent: #2fd97a;
    --ink: #f4f4f2;
    --frame: #1f3a3a;
  }
  * { box-sizing: border-box; margin: 0; padding: 0; }
  html, body { width: 1200px; height: 900px; overflow: hidden; }
  body {
    background: var(--backdrop);
    font-family: "Poppins", sans-serif;
    color: var(--ink);
    display: flex;
    flex-direction: column;
    align-items: center;
    justify-content: center;
    gap: 40px;
  }
  .card {
    position: relative;
    width: 640px;
    height: 366px;
    background: var(--card);
    box-shadow: 0 10px 30px rgba(0,0,0,.5);
    overflow: hidden;
  }
  .card__band {
    position: absolute;
    left: 0; right: 0; bottom: 0;
    height: 14px;
    background: var(--accent);
  }

  /* Front */
  .card--front .brand {
    position: absolute;
    left: 50%; top: 44%;
    transform: translate(-50%, -50%);
    display: flex;
    align-items: center;
    gap: 22px;
    padding: 26px 40px;
    border: 1px solid var(--frame);
    border-radius: 14px;
  }
  .brand__mark {
    width: 58px; height: 58px;
    background: var(--accent);
  }
  .brand__name {
    font-weight: 600;
    font-size: 30px;
    line-height: 1.1;
    letter-spacing: 1px;
    text-transform: uppercase;
    color: var(--ink);
  }

  /* Back */
  .card--back .identity {
    position: absolute;
    left: 44px; top: 150px;
    width: 250px;
    text-align: right;
  }
  .identity__name {
    font-family: "Oswald", sans-serif;
    font-weight: 500;
    font-size: 34px;
    line-height: 1;
    color: var(--accent);
    text-transform: uppercase;
  }
  .identity__role {
    font-size: 15px;
    margin-top: 4px;
  }
  .divider {
    position: absolute;
    left: 318px; top: 148px;
    width: 1.5px; height: 86px;
    background: var(--accent);
  }
  .contacts {
    position: absolute;
    left: 340px; top: 160px;
    list-style: none;
    font-size: 14.5px;
    line-height: 24px;
  }
  .contacts li { display: flex; align-items: center; gap: 8px; }
  .contacts svg { width: 15px; height: 15px; flex: none; }
  .address {
    position: absolute;
    left: 0; right: 0; top: 272px;
    text-align: center;
    font-size: 15px;
  }
</style>
</head>
<body>
  <section class="card card--front" aria-label="Card front">
    <div class="brand">
      <span class="brand__mark"></span>
      <span class="brand__name">Ridgeline<br>Construction</span>
    </div>
    <div class="card__band"></div>
  </section>

  <section class="card card--back" aria-label="Card back">
    <div class="identity">
      <p class="identity__name">Daniel Porter</p>
      <p class="identity__role">Managing Director</p>
    </div>
    <div class="divider"></div>
    <ul class="contacts">
      <li>
        <svg viewBox="0 0 24 24" fill="none" stroke="#2fd97a" stroke-width="2.2" stroke-linecap="round" stroke-linejoin="round"><path d="M5 3h4l2 5-2.5 1.5a11 11 0 0 0 6 6L16 13l5 2v4a2 2 0 0 1-2 2A16 16 0 0 1 3 5a2 2 0 0 1 2-2z"/></svg>
        044-555 210 374
      </li>
      <li>
        <svg viewBox="0 0 24 24" fill="none" stroke="#2fd97a" stroke-width="2.2" stroke-linejoin="round"><rect x="2" y="5" width="20" height="14"/><path d="M2 5l10 8 10-8"/></svg>
        hello@ridgelinebuild.com
      </li>
      <li>
        <svg viewBox="0 0 24 24" fill="none" stroke="#2fd97a" stroke-width="2"><circle cx="12" cy="12" r="10"/><ellipse cx="12" cy="12" rx="4.5" ry="10"/><path d="M2 12h20M4 7h16M4 17h16"/></svg>
        www.ridgelinebuild.com
      </li>
    </ul>
    <p class="address">88, Harbor Ridge Road, Easton, 45190</p>
    <div class="card__band"></div>
  </section>
</body>
</html>
```